Elevating our current Business Card Design

We want to elevate our current business card with a new design to look like a zenith 300 company. We are a premium lubricant distributor (oil and grease).
We need 2 versions, version 1 is as per the uploaded a copy of our current business card with the English version.
For our Chinese version we need to use the front to be English in English and have the back of the card designed exactly like the front for all info to be in Chinese.
The design template needs to be such that we can amend the template with adding different information for each person's card.
The background colour of the card can be changed- we just need to clearly see all information on the card and logos.
The QJR and Ember steady logos cannot have any colour or display changes- only use the logos attached.
All logos need to be included and all information from the attached current card

```html
<!DOCTYPE html>
<html lang="en">
<head>
<meta charset="utf-8">
<title>Meridian Oil Distributors – Business Card</title>
<link rel="stylesheet" href="https://fonts.googleapis.com/css2?family=Open+Sans:wght@400;600;700;800&display=swap">
<style>
  :root {
    --canvas: #1c1c1f;
    --card: #232226;
    --card-edge: #e3262b;
    --red: #e8262c;
    --orange: #f08a24;
    --white: #ffffff;
    --grey: #8d8d92;
    --emboss: #141416;
  }
  * { box-sizing: border-box; margin: 0; padding: 0; }
  html, body { width: 1200px; height: 780px; overflow: hidden; }
  body {
    background: var(--canvas);
    font-family: "Open Sans", Arial, sans-serif;
    display: flex;
    align-items: center;
    justify-content: center;
    gap: 40px;
  }
  .card {
    position: relative;
    width: 540px;
    height: 330px;
    background: var(--card);
    border-radius: 26px;
    border-bottom: 4px solid var(--card-edge);
    border-left: 2px solid var(--card-edge);
    border-right: 2px solid var(--card-edge);
    overflow: hidden;
    box-shadow: 0 20px 40px rgba(0,0,0,.45);
  }

  /* Front */
  .front-brand {
    position: absolute;
    inset: 0;
    display: flex;
    align-items: center;
    justify-content: center;
    gap: 26px;
  }
  .front-brand__dot {
    width: 70px; height: 70px;
    border-radius: 50%;
    background: var(--orange);
  }
  .front-brand__name {
    font-size: 120px;
    font-weight: 800;
    color: var(--emboss);
    letter-spacing: -2px;
  }

  /* Back */
  .tab {
    position: absolute;
    top: 0; right: 0;
    width: 14px; height: 40px;
    background: var(--red);
  }
  .contact {
    position: absolute;
    top: 22px; right: 34px;
    text-align: right;
    color: var(--white);
  }
  .contact__name {
    font-size: 30px;
    font-weight: 700;
    color: var(--red);
    line-height: 1.05;
  }
  .contact__title { font-size: 14px; margin-bottom: 10px; }
  .contact__address { font-size: 13px; line-height: 1.35; margin-bottom: 10px; }
  .contact__lines { display: flex; gap: 10px; }
  .contact__list { list-style: none; font-size: 13px; line-height: 1.55; }
  .contact__icons { list-style: none; line-height: 1.55; }
  .contact__icons li { height: 20px; display: flex; align-items: center; }
  .contact__icons svg { width: 12px; height: 12px; fill: var(--red); }

  .badges {
    position: absolute;
    right: 30px; bottom: 26px;
    display: flex;
    align-items: center;
    gap: 18px;
  }
  .badge-eco { width: 60px; height: 34px; border-radius: 6px; background: var(--white); }
  .badge-cert { width: 36px; height: 36px; border-radius: 50%; background: var(--orange); border: 3px solid var(--grey); }

  .ribbon {
    position: absolute;
    left: 0; bottom: 0;
    width: 250px;
  }
  .ribbon__panel {
    background: var(--white);
    padding: 14px 16px;
    display: flex;
    align-items: center;
    gap: 10px;
  }
  .ribbon__mark { width: 14px; height: 14px; border-radius: 50%; background: var(--red); }
  .ribbon__name { font-size: 13px; font-weight: 700; color: var(--red); line-height: 1.15; }
  .ribbon__band {
    background: var(--red);
    color: var(--white);
    padding: 8px 16px 12px;
  }
  .ribbon__brand { font-size: 20px; font-weight: 800; letter-spacing: 1px; }
  .ribbon__tagline { font-size: 10px; letter-spacing: 1.5px; text-transform: uppercase; }
</style>
</head>
<body>

  <section class="card card--front" aria-label="Card front">
    <div class="front-brand">
      <span class="front-brand__dot"></span>
      <span class="front-brand__name">MOD</span>
    </div>
  </section>

  <section class="card card--back" aria-label="Card back">
    <span class="tab"></span>

    <div class="contact">
      <h1 class="contact__name">Mara Volkov</h1>
      <p class="contact__title">Administration Executive</p>
      <p class="contact__address">14 Harbour Freight Way<br>Ashcombe, WA 6199</p>
      <div class="contact__lines">
        <ul class="contact__list">
          <li>1300 482 617</li>
          <li>+61 400 218 903</li>
          <li>+61 8 9000 4127</li>
          <li>www.meridianoil.com</li>
          <li>mara.volkov@meridianoil.com</li>
        </ul>
        <ul class="contact__icons" aria-hidden="true">
          <li><svg viewBox="0 0 12 12"><path d="M2 1h3l1 3-2 1a7 7 0 0 0 3 3l1-2 3 1v3c-6 0-9-3-9-9z"/></svg></li>
          <li><svg viewBox="0 0 12 12"><rect x="3" y="0" width="6" height="12" rx="1"/></svg></li>
          <li><svg viewBox="0 0 12 12"><rect x="1" y="3" width="10" height="8" rx="1"/><rect x="3" y="0" width="6" height="3"/></svg></li>
          <li><svg viewBox="0 0 12 12"><circle cx="6" cy="6" r="5.5"/></svg></li>
          <li><svg viewBox="0 0 12 12"><path d="M0 2h12v8H0zM1 3l5 4 5-4"/></svg></li>
        </ul>
      </div>
    </div>

    <div class="badges">
      <span class="badge-eco" role="img" aria-label="Ember steady network member badge"></span>
      <span class="badge-cert" role="img" aria-label="QJR certification badge"></span>
      <span class="badge-cert" role="img" aria-label="QJR certification badge"></span>
      <span class="badge-cert" role="img" aria-label="QJR certification badge"></span>
    </div>

    <div class="ribbon">
      <div class="ribbon__panel">
        <span class="ribbon__mark"></span>
        <span class="ribbon__name">Meridian Oil<br>Distributors</span>
      </div>
      <div class="ribbon__band">
        <div class="ribbon__brand">KESTREL</div>
        <div class="ribbon__tagline">Premium Lubricants</div>
      </div>
    </div>
  </section>

</body>
</html>
```